BRAMBLEFORD CONSTRUCTIONS B-Card

I currently have a b-card design but will be removing the image (tree) from the logo and have text only.
I want the card to be classy and strong within the building and construction industry.
I will be using Spot UV on the cards as per the attached examples. I will also send through some sketched ideas that I have in mind.
The color blue is similar to the image (No. 6) attached images

Target Market(s)

middle to maturre aged.
Home Owners / Renovators and Builders

Industry/Entity Type

Construction

Contact Information for Business Card

BRAMBLEFORD CONSTRUCTIONS
Name: Gareth Pennick
Title: Project Manager
Mobile: 0427 351 804
Office: (08) 9316 5172
Address: 47C Corvell Street, Malaga WA 6090
Email: info@bramblefordhomes.com.au
PO Box: 3817 Malaga WA 6944

Colors
0592cd
33a6d7
85cae6
1b1b1b

Requirements
Must have
• 1. It must have spot UV on the front of card, maybe back of card too
• 2. I really like the blue on image 6. (or at least a really cool electric blue against the charcoal grey background)
• 3. The font must be slimline and modern. Easy to read
• 4. There must be no black used on the card... Only greys and dark charcoal greys
• 5. Use only the text from the logo "Brambleford Constructions" Not the image of the tree. I am wanting the b-cards to be more masculine.
Nice to have
• 1. I like the design concept on image 6. but happy to see what else you can do with the Spot UV
• 2. Unless you have a really cool idea of the image of the tree (from previous logo) Spot UV somewhere in the design concept thats original and different then I am keen to see what you come up with
• 3. Try changing the color of the logo eg. full white or Blue and white
• 4. Another option is to have the Brambleford Logo on the front of card with the spot UV in the background of text which we specialise in eg, Roofing, Ceiling, Insulation, Gutter Guards, Electrical, Insurance etc and we can add or reduce items as required. Similar to image 12.
Should not have
• Do not include the image of the tree from previous logo. unless you have a really cool idea of Spot UV somewhere in the design concept thats original and different.

```html
<!DOCTYPE html>
<html lang="en">
<head>
<meta charset="utf-8">
<title>Brambleford Constructions Business Card</title>
<link href="https://fonts.googleapis.com/css2?family=Open+Sans:wght@400;600&display=swap" rel="stylesheet">
<style>
  :root {
    --page-bg: #e4e1dc;
    --card-bg: #282828;
    --electric-blue: #33a6d7;
    --text-light: #f2f2f2;
    --spot-uv: #1c1c1c;
    --tree-tone: #3a3a3a;
  }
  * { box-sizing: border-box; margin: 0; padding: 0; }
  html, body {
    width: 1200px; height: 1000px; overflow: hidden;
    background: var(--page-bg);
    font-family: "Open Sans", Arial, sans-serif;
  }
  .card {
    position: absolute; left: 265px; width: 665px; height: 397px;
    background: var(--card-bg);
    box-shadow: 0 4px 14px rgba(0,0,0,.25);
  }
  .card--front { top: 73px; }
  .card--back { top: 532px; }

  .wordmark { position: absolute; text-align: right; font-weight: 600; color: var(--electric-blue); }
  .card--front .wordmark { right: 32px; top: 44px; }
  .wordmark__main { display: block; font-size: 40px; line-height: 44px; letter-spacing: 0.5px; }
  .wordmark__sub { display: block; font-size: 17px; line-height: 22px; letter-spacing: 7.4px; margin-right: -7px; }

  .card--back .wordmark {
    left: 0; right: 0; top: 150px; text-align: center; color: var(--spot-uv);
  }
  .card--back .wordmark__main { font-size: 54px; line-height: 60px; }
  .card--back .wordmark__sub { font-size: 21px; line-height: 28px; letter-spacing: 12px; margin-right: -12px; }

  .tree-area {
    position: absolute; left: 363px; top: 127px; width: 233px; height: 240px;
    border-radius: 50%;
    background: radial-gradient(circle, var(--tree-tone) 0%, #2d2d2d 60%, var(--card-bg) 72%);
  }

  .contact { position: absolute; left: 33px; top: 170px; color: var(--text-light); }
  .contact__name { font-size: 19px; font-weight: 600; color: var(--electric-blue); line-height: 26px; }
  .contact__title { font-size: 16px; line-height: 22px; color: var(--text-light); }
  .contact__list { list-style: none; margin-top: 15px; }
  .contact__item { display: flex; align-items: center; font-size: 16px; line-height: 25px; }
  .contact__icon { width: 16px; height: 14px; margin-right: 8px; fill: var(--electric-blue); }
  .contact__address { margin-top: 6px; font-size: 16px; line-height: 25px; }
</style>
</head>
<body>
  <section class="card card--front">
    <div class="wordmark">
      <span class="wordmark__main">BRAMBLEFORD</span>
      <span class="wordmark__sub">CONSTRUCTIONS</span>
    </div>

    <div class="tree-area" role="img" aria-label="Spot UV tree with roots illustration"></div>

    <div class="contact">
      <p class="contact__name">GARETH PENNICK</p>
      <p class="contact__title">Project Manager</p>
      <ul class="contact__list">
        <li class="contact__item">
          <svg class="contact__icon" viewBox="0 0 16 14" aria-hidden="true"><path d="M5 0h6v14H5z M6 1v10h4V1z M7.5 12h1v1h-1z" fill-rule="evenodd"/></svg>
          0427 351 804
        </li>
        <li class="contact__item">
          <svg class="contact__icon" viewBox="0 0 16 14" aria-hidden="true"><path d="M1 4c2-3 12-3 14 0l-1 2-3-1V3H5v2L2 6z M3 7h10l1 6H2z"/></svg>
          (08) 9316 5172
        </li>
        <li class="contact__item">
          <svg class="contact__icon" viewBox="0 0 16 14" aria-hidden="true"><path d="M1 3h14v9H1z M1 3l7 5 7-5"/></svg>
          info@bramblefordhomes.com.au
        </li>
      </ul>
      <p class="contact__address">PO Box 3817 Dunmarra WA 6581<br>47C Corvell Street, Dunmarra WA 6472</p>
    </div>
  </section>

  <section class="card card--back">
    <div class="wordmark">
      <span class="wordmark__main">BRAMBLEFORD</span>
      <span class="wordmark__sub">CONSTRUCTIONS</span>
    </div>
  </section>
</body>
</html>
```